Private Investigation Business Card Design

I need a business card for a new private investigation company named Brisk Inquiries. I perform mainly surveillance jobs, vehicle repossessions, document serves etc. The final design should aim for a professional look. The logo has a magnifying glass with stick man arms and legs and is in a running action to show the "Brisk" aspect of the name. If the colour scheme could remain the same as the website www.briskinquiries-demo.com.au with silvers,blacks and a couple electric blue highlights.
Industry/Entity Type
Business
Contact Information for Business Card
Morgan Kellaway
Brisk Inquiries
0487316204
PO Box 58, Carnwell NSW 2291
info@briskinquiries-demo.com.au
www.briskinquiries-demo.com.au
Look and feel

```html
<!DOCTYPE html>
<html lang="en">
<head>
<meta charset="utf-8">
<title>Brisk Inquiries – Business Card</title>
<link rel="stylesheet" href="https://fonts.googleapis.com/css2?family=Arimo:wght@400;700&display=swap">
<style>
  :root {
    --stage: #2a2a2c;
    --card-white: #ffffff;
    --card-white-shade: #e9e9e9;
    --silver-light: #dcdcdc;
    --silver-mid: #a9a9a9;
    --silver-dark: #7d7d7d;
    --ink: #1b1b1b;
    --ink-soft: #3a3a3a;
    --text-grey: #555555;
    --brand-silver: #8e8e8e;
  }
  * { margin: 0; padding: 0; box-sizing: border-box; }
  html, body { width: 1200px; height: 871px; overflow: hidden; }
  body {
    background: var(--stage);
    font-family: "Arimo", Arial, sans-serif;
    position: relative;
  }
  .card {
    position: absolute;
    left: 290px;
    width: 620px;
    height: 354px;
    overflow: hidden;
  }
  /* Back side */
  .card-back {
    top: 51px;
    background: linear-gradient(160deg, var(--silver-light) 0%, var(--silver-mid) 55%, var(--silver-dark) 100%);
  }
  .back-brand {
    position: absolute;
    left: 0; right: 0; top: 138px;
    display: flex; align-items: center; justify-content: center; gap: 14px;
  }
  .back-brand .brand-dot {
    width: 34px; height: 34px; border-radius: 50%;
    background: var(--ink);
  }
  .back-brand .brand-name {
    font-size: 40px; font-weight: 700; color: var(--ink);
  }
  .back-web {
    position: absolute; right: 34px; bottom: 26px;
    font-size: 13px; letter-spacing: 2px; color: var(--ink-soft);
  }
  /* Front side */
  .card-front {
    top: 465px;
    background: linear-gradient(170deg, var(--card-white) 0%, var(--card-white) 60%, var(--card-white-shade) 100%);
  }
  .front-brand {
    position: absolute; left: 40px; top: 34px;
    display: flex; align-items: center; gap: 12px;
  }
  .front-brand .brand-name {
    font-size: 40px; font-weight: 700; color: var(--brand-silver);
    letter-spacing: 0.5px;
  }
  .front-brand .brand-dot {
    width: 22px; height: 22px; border-radius: 50%;
    background: var(--brand-silver);
  }
  .contact {
    position: absolute; left: 40px; top: 128px;
    font-size: 15px; color: var(--text-grey); line-height: 1.3;
  }
  .contact .address { margin-bottom: 10px; }
  .contact-row { display: flex; align-items: center; gap: 9px; height: 24px; }
  .contact-row svg { width: 14px; height: 14px; fill: var(--ink); flex: none; }
  .name-bar {
    position: absolute; left: 394px; right: 0; top: 254px; height: 48px;
    background: linear-gradient(180deg, #f2f2f2 0%, #bdbdbd 55%, #9a9a9a 100%);
    border-top: 1px solid #8a8a8a;
    border-left: 1px solid #8a8a8a;
    border-bottom: 1px solid #707070;
    display: flex; align-items: center; padding-left: 26px;
  }
  .name-bar .holder {
    font-size: 18px; font-weight: 700; color: var(--ink);
  }
</style>
</head>
<body>

  <section class="card card-back" aria-label="Card back">
    <div class="back-brand">
      <span class="brand-dot"></span>
      <span class="brand-name">Brisk Inquiries</span>
    </div>
    <p class="back-web">www.briskinquiries-demo.com.au</p>
  </section>

  <section class="card card-front" aria-label="Card front">
    <div class="front-brand">
      <span class="brand-name">Brisk Inquiries</span>
      <span class="brand-dot"></span>
    </div>

    <div class="contact">
      <p class="address">PO Box 58<br>Carnwell NSW 2291</p>
      <div class="contact-row">
        <svg viewBox="0 0 16 16" aria-hidden="true"><path d="M3 1h3l1 4-2 1c1 2 3 4 5 5l1-2 4 1v3c0 1-1 2-2 2C7 15 1 9 1 3c0-1 1-2 2-2z"/></svg>
        <span>0487 316 204</span>
      </div>
      <div class="contact-row">
        <svg viewBox="0 0 16 16" aria-hidden="true"><path d="M1 3h14v10H1z M2 4l6 5 6-5" fill="none" stroke="#1b1b1b" stroke-width="1.6"/><path d="M1 3h14L8 8.5z"/></svg>
        <span>info@briskinquiries-demo.com.au</span>
      </div>
      <div class="contact-row">
        <svg viewBox="0 0 16 16" aria-hidden="true"><circle cx="8" cy="8" r="7"/><path d="M5 5c2 0 2 2 4 2s1 3 3 3" fill="none" stroke="#ffffff" stroke-width="1.4"/></svg>
        <span>www.briskinquiries-demo.com.au</span>
      </div>
    </div>

    <div class="name-bar">
      <span class="holder">Morgan Kellaway</span>
    </div>
  </section>

</body>
</html>
```